A new fresh and flat K&T Logistics Brochure Design A4 - 4 pages

Our client is an established International Logistics firm looking to upgrade their sales brochure.
We would like the designer to create concepts that are flat, modern and communicate reliability and expediency to our clients. We want the brochure to maintain a degree of white space and minimal design.
Introduction
LOGISTICS - it's what we do best! We're proud to say so after 27 years (and counting) of organic growth within the 3PL industry. Starting off in Meridian, Mississippi with a fleet of 4 trucks in 1987, K&T is today a global 3PL company with offices in the United States and Asia Pacific region.
Our goal has always been to serve our clients by getting things done, and getting them done right.
Format: A4 4-sided brochure
Pg 1 Front Page - Company name and logo, and vector design concept to make front page unique. Please try to include some kind of container reference design on the front page (e.g 2D or 3D vector, transparent overlay etc...), place this design element somewhere in the middle or bttom of the page.
Pg 2 and/or Pg 3
- Introduction and Core services Including: ABOUT, SERVICES, CONTRACT LOGISTICS, K&T INTEL (following the menu content of our website www.ktvfr.example)
- Text space to explain Services in more detail.
Social proof (existing client testimonials/feedback.)
- A 'C.A.R.E' acronym design element, including the words: Communicative, Accessible, Responsible, Efficient
Pg 4 Back Page- Contact information, Call to action.
Throughut the brochure please leave space for images as you deem appropriate and we will update late OR even better usesome of your own stock images.
Color theme: Based on corporate colors (but not limited to), see website
http://www.ktvfr.example
Try diffent font types to the website both serif and sans serif
Include several CTAs throughout the brochure.
You can use both the attached pdf brochure and the website for content.
We would also appreciate if you could also enhance the logo to make it 'pop' (keep shape and style).

```html
<!DOCTYPE html>
<html lang="en">
<head>
<meta charset="utf-8">
<title>K&amp;T Logistics – Back Cover</title>
<link rel="stylesheet" href="https://fonts.googleapis.com/css2?family=Oswald:wght@500;600&family=Arimo:ital,wght@0,400;0,700;1,700&family=Roboto:wght@500&display=swap">
<style>
  :root {
    --slate: #647f98;
    --slate-light: #8ea1b6;
    --orange: #f7941d;
    --ink: #1e1e1e;
    --paper: #ffffff;
    --hatch: #c9d0d8;
  }
  html, body { margin: 0; padding: 0; overflow: hidden; background: var(--paper); }
  p, h1 { margin: 0; }
  .page { position: relative; width: 1200px; height: 849px; overflow: hidden; background: var(--paper); font-family: "Arimo", Arial, sans-serif; color: var(--ink); }
  .page-shapes { position: absolute; inset: 0; }
  .brand { position: absolute; left: 850px; top: 244px; }
  .brand-name { font-family: "Arimo", Arial, sans-serif; font-weight: 700; font-size: 44px; line-height: 1; color: var(--slate-light); letter-spacing: 1px; }
  .brand-tagline { position: absolute; left: 946px; top: 280px; font-family: "Arimo", Arial, sans-serif; font-style: italic; font-weight: 700; font-size: 12.5px; line-height: 14px; color: var(--slate); white-space: nowrap; }
  .contact-title { position: absolute; left: 64px; top: 334px; font-family: "Oswald", "Arial Narrow", sans-serif; font-weight: 600; font-size: 28px; line-height: 1.2; color: var(--orange); }
  .office { position: absolute; font-size: 9.6px; line-height: 12.2px; white-space: nowrap; }
  .office-region { font-family: "Oswald", "Arial Narrow", sans-serif; font-weight: 500; font-size: 10.5px; line-height: 13px; display: block; }
  .office--china { left: 64px; top: 384px; }
  .office--usa { left: 64px; top: 462px; }
  .office--hongkong { left: 268px; top: 384px; }
  .office-email { position: absolute; left: 268px; top: 464px; font-family: "Roboto", Arial, sans-serif; font-weight: 500; font-size: 9.8px; }
  .web-address { position: absolute; left: 860px; top: 792px; font-family: "Oswald", "Arial Narrow", sans-serif; font-weight: 500; font-size: 12px; color: var(--orange); }
</style>
</head>
<body>
<main class="page">
  <svg class="page-shapes" width="1200" height="849" viewBox="0 0 1200 849">
    <defs>
      <pattern id="hatch-lines" width="6" height="34" patternUnits="userSpaceOnUse" patternTransform="skewX(-30)">
        <line x1="1" y1="0" x2="1" y2="34" stroke="var(--hatch)" stroke-width="1"/>
      </pattern>
      <pattern id="hatch-lines-dark" width="6" height="34" patternUnits="userSpaceOnUse" patternTransform="skewX(-30)">
        <line x1="1" y1="0" x2="1" y2="34" stroke="#ffffff" stroke-opacity="0.55" stroke-width="1"/>
      </pattern>
      <linearGradient id="yard-photo" x1="0" y1="0" x2="0" y2="1">
        <stop offset="0" stop-color="#5d8fd6"/>
        <stop offset="0.45" stop-color="#2f5fb8"/>
        <stop offset="0.7" stop-color="#d8dde0"/>
        <stop offset="1" stop-color="#a7a39b"/>
      </linearGradient>
    </defs>
    <polygon class="panel-top" points="0,0 878,0 699,310 0,310" fill="var(--slate)"/>
    <polygon class="panel-bottom" points="0,549 561,549 388,849 0,849" fill="var(--slate)"/>
    <polygon class="hatch-band hatch-band--upper" points="88,257 828,257 808,291 68,291" fill="url(#hatch-lines)"/>
    <polygon class="hatch-band hatch-band--upper-dark" points="88,257 718,257 699,291 68,291" fill="url(#hatch-lines-dark)"/>
    <polygon class="hatch-band hatch-band--lower" points="350,568 1080,568 1060,602 330,602" fill="url(#hatch-lines)"/>
    <polygon class="cover-photo" role="img" aria-label="Photo of a white semi truck hauling a blue shipping container in a freight yard" points="690,310 1200,310 1200,549 553,549" fill="url(#yard-photo)"/>
    <polygon class="photo-cut" points="1148,310 1160,310 1034,549 1022,549" fill="var(--paper)"/>
  </svg>

  <div class="brand"><span class="brand-name">K&amp;T</span></div>
  <p class="brand-tagline">Logistics and Supply Chain Solutions</p>

  <h1 class="contact-title">Contact US</h1>

  <p class="office office--china">
    <span class="office-region">China</span>
    K&amp;T Logistics<br>
    18F, Harbour Tower, Linhai Road, Nanshan<br>
    District, Shenzhen 518000,<br>
    Telephone: +86 755 0000 1234
  </p>

  <p class="office office--usa">
    <span class="office-region">USA</span>
    K&amp;T Transport<br>
    1200 Freightway Drive<br>
    Springfield, MS 39000 USA<br>
    Telephone: +1 555 010 2030
  </p>

  <p class="office office--hongkong">
    <span class="office-region">Hong Kong</span>
    K&amp;T Logistics<br>
    12F Harbourview House<br>
    88 Sample Road, Central,<br>
    Telephone: +852 0000 5678
  </p>

  <p class="office-email">Email: info@ktlogistics.example</p>

  <p class="web-address">www.ktvfr.example</p>
</main>
</body>
</html>
```